A private security company called "Tavron Security Services Ltd"

Hello everybody,

We need a web page for a company based in NZ. It is mainly an informative website so it would be wonderful if the designer puts their absolute best into making it a website that I would really appreciate. The website needs to show professionalism and also needs to make our web surfers find the information they need in a click. the company's colour is black and silver, and if those two colours could be integrated into the website it would be absolutely lovely. Please do contact me for any information.

Sincerely,
Dorian Vaskel

Industry/Entity Type

Security

```html
<!DOCTYPE html>
<html lang="en">
<head>
<meta charset="utf-8">
<title>Tavron Security Services Ltd</title>
<link href="https://fonts.googleapis.com/css2?family=Cinzel:wght@600;700&family=Source+Sans+3:wght@400;600&display=swap" rel="stylesheet">
<style>
:root{
  --page:#c4c5c9;
  --ink:#1b1b1b;
  --text:#2f2f2f;
  --muted:#7a7a7a;
  --nav:#1a1a1a;
  --nav-active:#3c3c3c;
  --nav-line:#444;
  --white:#ffffff;
  --silver:#dcdcdc;
  --box-line:#c9c9c9;
  --footer:#000000;
  --footer-text:#dcdcdc;
}
*{box-sizing:border-box;margin:0;padding:0}
html,body{width:1200px;height:1116px;overflow:hidden}
body{position:relative;background:var(--page);font-family:"Source Sans 3",Arial,sans-serif;color:var(--text)}
.site-header{position:absolute;left:0;top:0;width:1200px;height:160px;background:linear-gradient(#fff,#f4f4f4);box-shadow:0 2px 4px rgba(0,0,0,.25)}
.brand{position:absolute;left:102px;top:30px;display:flex;align-items:center;gap:10px}
.brand-mark{width:44px;height:44px;border-radius:50%;background:var(--ink)}
.brand-name{font-weight:600;color:var(--ink);font-size:24px;line-height:1;letter-spacing:1px}
.brand-name small{display:block;font-size:12px;letter-spacing:.3px;margin-top:4px}
.call{position:absolute;left:786px;top:40px}
.call svg{position:absolute;left:0;top:4px}
.call-title{position:absolute;left:72px;top:0;font-family:"Cinzel",serif;font-weight:700;font-size:26px;color:var(--ink);white-space:nowrap}
.call-number{position:absolute;left:68px;top:30px;font-size:25px;color:#333;white-space:nowrap}
.main-nav{position:absolute;left:100px;top:120px;width:1002px;height:40px;background:var(--nav);border-radius:4px 4px 0 0;display:flex;overflow:hidden}
.main-nav a{display:flex;align-items:center;justify-content:center;color:#eee;text-decoration:none;font-size:15px;letter-spacing:.6px;border-left:1px solid var(--nav-line)}
.main-nav a:first-child{border-left:0;background:var(--nav-active)}
.hero{position:absolute;left:100px;top:160px;width:1002px;height:346px;background:linear-gradient(90deg,#fafafa 0%,#f1f1f1 45%,#b08868 62%,#5a3f2e 72%,#2a2a30 85%,#16161a 100%)}
.hero-title{position:absolute;left:28px;top:104px;font-family:"Cinzel",serif;font-weight:700;font-size:64px;color:var(--ink)}
.hero-sub{position:absolute;left:30px;top:188px;font-size:24px;color:var(--muted);letter-spacing:.5px}
.content{position:absolute;left:100px;top:506px;width:1002px;height:496px;background:var(--white);border-left:1px solid #ddd;border-right:1px solid #ddd}
.welcome{position:absolute;left:0;top:26px;width:1002px;text-align:center;font-family:"Cinzel",serif;font-weight:700;font-size:36px;color:var(--ink)}
.intro{position:absolute;left:50px;top:84px;width:902px;text-align:center;font-size:14px;line-height:22px}
.intro p+p{margin-top:22px}
.rule{position:absolute;left:28px;top:268px;width:941px;height:1px;background:#ccc}
.service{position:absolute;top:296px;width:147px;height:159px}
.service-badge{position:absolute;left:39px;top:0;width:72px;height:72px;border-radius:50%;background:radial-gradient(#fff 55%,#e4e4e4);border:3px solid #222;box-shadow:0 2px 3px rgba(0,0,0,.3);z-index:2}
.service-box{position:absolute;left:0;top:50px;width:147px;height:109px;border:1px solid var(--box-line);background:linear-gradient(#fff,var(--silver));display:flex;align-items:center;justify-content:center;text-align:center;padding:20px 6px 0;font-size:13px;line-height:17px;color:#222;text-transform:uppercase}
.site-footer{position:absolute;left:0;top:1002px;width:1200px;height:114px;background:var(--footer);color:var(--footer-text);font-size:14px;text-align:center}
.footer-links{position:absolute;left:148px;top:36px;white-space:nowrap}
.footer-links a{color:var(--footer-text);text-decoration:none}
.footer-links span{margin:0 13px}
.copyright{position:absolute;left:0;width:1220px;top:68px}
</style>
</head>
<body>
<header class="site-header">
  <div class="brand">
    <div class="brand-mark"></div>
    <div class="brand-name">TAVRON<small>Security Services Ltd.</small></div>
  </div>
  <div class="call">
    <svg width="60" height="60" viewBox="0 0 60 60" aria-hidden="true">
      <path d="M6 6h10v40c0 6 4 9 8 9" fill="none" stroke="#222" stroke-width="4"/>
      <rect x="20" y="4" width="38" height="48" rx="5" fill="#222"/>
      <rect x="27" y="10" width="24" height="10" fill="#fff"/>
      <g fill="#fff"><rect x="27" y="25" width="6" height="5"/><rect x="36" y="25" width="6" height="5"/><rect x="45" y="25" width="6" height="5"/><rect x="27" y="33" width="6" height="5"/><rect x="36" y="33" width="6" height="5"/><rect x="45" y="33" width="6" height="5"/><rect x="27" y="41" width="6" height="5"/><rect x="36" y="41" width="6" height="5"/><rect x="45" y="41" width="6" height="5"/></g>
    </svg>
    <div class="call-title">Call Us</div>
    <div class="call-number">+1 (456) 7302-48-615</div>
  </div>
  <nav class="main-nav">
    <a style="width:104px">HOME</a>
    <a style="width:148px">ABOUT US</a>
    <a style="width:140px">TRAINING</a>
    <a style="width:128px">SAFETY</a>
    <a style="width:184px">SUSTAINABILITY</a>
    <a style="width:159px">CONTACT US</a>
    <a style="width:139px">CAREERS</a>
  </nav>
</header>

<section class="hero" role="img" aria-label="Photo of a security guard's hand holding a two-way radio at his belt">
  <h1 class="hero-title">Experts</h1>
  <p class="hero-sub">IN YOUR INTERESTS PROTECTION</p>
</section>

<main class="content">
  <h2 class="welcome">Welcome to Tavron</h2>
  <div class="intro">
    <p>Lorem Ipsum is simply Lorem Ipsum has been the industry's standard dummy text ever since the 1500s, when an unknown printer took a galley of type and scrambled it to make book. It has survived not only five centuries, but also the leap into electronic typesetting, remaining has been the industry's standard dummy text ever since the 1500s, when an unknown printer took a galley of type and scrambled it to making book. It has survived not only five centuries, but also the leap into electronic essentially unchanged.</p>
    <p>It has survived not only five centuries, but also the leap into electronic typesetting, remaining has been the industry's standard dummy text ever since the 1500s, when an unknown printer took a galley remaining has been the industry's standard</p>
  </div>
  <div class="rule"></div>
  <div class="service" style="left:28px"><div class="service-badge"></div><div class="service-box">Property<br>Guards</div></div>
  <div class="service" style="left:228px"><div class="service-badge"></div><div class="service-box">Corporate Events<br>Security</div></div>
  <div class="service" style="left:427px"><div class="service-badge"></div><div class="service-box">Personal Body Guard for High Net Worth Individuals</div></div>
  <div class="service" style="left:627px"><div class="service-badge"></div><div class="service-box">Security<br>Consultancy</div></div>
  <div class="service" style="left:826px"><div class="service-badge"></div><div class="service-box">Private<br>Investigation</div></div>
</main>

<footer class="site-footer">
  <div class="footer-links">
    <a>Property guards</a><span>|</span><a>Corporate events security</a><span>|</span><a>Personal bodyguard for high net worth individuals</a><span>|</span><a>Security consultancy</a><span>|</span><a>Private investigation</a>
  </div>
  <p class="copyright">Copyright © 2014 Tavron Security Services LTD.</p>
</footer>
</body>
</html>
```